I need a fresh looking, exciting and loaded design for Full service Restaurant

We need a web design for our restaurant, which offers full service Pakistani and Indian food in PA, USA. Design should be elegant, simplified so customers can navigate easily and order food online for catering as well as delivery. We need loads of pictures and room to grow. I already have a web address via vemrilo.com. It should include SSL and e-commerce for ordering food.
Be original and be creative and make it a fun site :)

```html
<!DOCTYPE html>
<html lang="en">
<head>
<meta charset="utf-8">
<title>Saffron Lane — A fine Pak-Indian Cuisine</title>
<link rel="stylesheet" href="https://fonts.googleapis.com/css2?family=Lobster+Two:ital,wght@0,700;1,700&family=Open+Sans:wght@400;600;700&display=swap">
<style>
:root{
  --green:#275211;
  --green-dark:#1f420c;
  --red:#d6202a;
  --ink:#333333;
  --muted:#7a7a7a;
  --line:#e3e3e3;
  --backdrop:#e9c896;
  --footer:#262626;
  --white:#ffffff;
}
*{box-sizing:border-box;margin:0;padding:0}
html,body{width:1200px;height:2203px;overflow:hidden}
body{background:var(--backdrop);font-family:"Open Sans",Arial,sans-serif;color:var(--ink);position:relative}
.page{position:absolute;left:98px;top:0;width:1004px;height:2203px;background:var(--white);box-shadow:0 0 12px rgba(0,0,0,.18)}
.script{font-family:"Lobster Two",cursive;font-style:italic;font-weight:700}

/* brand */
.brand{display:flex;align-items:center;gap:10px;white-space:nowrap}
.brand-dot{width:34px;height:34px;border-radius:50%;background:var(--green);flex:none}
.brand-name{font-family:"Lobster Two",cursive;font-weight:700;font-size:38px;color:var(--red);line-height:1}

/* header */
.site-header{position:relative;height:142px}
.header-brand{position:absolute;left:24px;top:32px}
.brand-tag{position:absolute;left:68px;top:80px;font-size:10px;color:var(--green);font-weight:600;white-space:nowrap}
.order-now{position:absolute;right:22px;top:52px;display:flex;align-items:center;gap:10px;font-size:19px;color:var(--green)}

/* nav */
.main-nav{position:absolute;top:142px;left:0;width:100%;height:59px;display:flex;border-top:1px solid var(--line);border-bottom:1px solid var(--line);background:#fafafa}
.main-nav a{flex:0 0 145px;display:flex;align-items:center;justify-content:center;border-right:1px solid var(--line);font-family:"Lobster Two",cursive;font-style:italic;font-weight:700;font-size:14px;color:#444;text-decoration:none}
.main-nav a:last-child{flex:1;border-right:0}
.main-nav a.active{background:var(--green);color:var(--white)}

/* hero */
.hero{position:absolute;top:201px;left:0;width:100%;height:506px;background:radial-gradient(ellipse at 35% 45%,#c8742f 0%,#8a4422 40%,#5a2f1d 75%,#3c2418 100%)}
.hero-copy{position:absolute;left:621px;top:200px;color:var(--white);white-space:nowrap}
.hero-copy .kicker{font-size:30px;font-weight:400;letter-spacing:1px;margin-left:10px}
.hero-copy .headline{font-size:38px;line-height:1.35;margin-left:10px;text-shadow:0 2px 6px rgba(0,0,0,.35)}
.slider-dots{position:absolute;right:24px;bottom:28px;display:flex;gap:10px;align-items:center}
.slider-dots span{width:10px;height:10px;border-radius:50%;background:var(--white)}
.slider-dots span.current{width:18px;height:18px;border:3px solid var(--white);background:transparent;box-shadow:inset 0 0 0 3px rgba(0,0,0,.25)}

/* services */
.services{position:absolute;top:707px;left:0;width:100%;height:445px}
.section-title{font-size:25px;color:var(--ink);position:absolute;left:24px}
.section-lead{position:absolute;left:24px;font-size:12.5px;color:#555}
.services .section-title{top:37px}
.services .section-lead{top:78px}
.pager{position:absolute;right:22px;top:48px;font-size:13px;color:#aaa;letter-spacing:6px}
.service-track{position:absolute;left:0;top:120px;width:100%;height:126px}
.service-card{position:absolute;top:0;width:250px}
.service-icon{width:123px;height:123px;border-radius:50%;display:flex;align-items:center;justify-content:center}
.service-icon .inner{width:101px;height:101px;border-radius:50%;border:3px solid var(--white);display:flex;align-items:center;justify-content:center}
.is-green .service-icon{background:var(--green)}
.is-green .service-icon .inner{background:var(--green)}
.is-red .service-icon{background:var(--red)}
.is-red .service-icon .inner{background:var(--red)}
.service-title{font-size:15px;margin-top:30px}
.is-green .service-title{color:var(--green)}
.service-text{font-size:11.5px;line-height:21px;color:var(--muted);margin-top:8px;width:245px}
.btn{display:inline-block;margin-top:20px;width:91px;height:35px;line-height:35px;text-align:center;color:var(--white);font-size:11px;font-weight:700;border-radius:3px;text-decoration:none}
.is-green .btn{background:var(--green)}
.is-red .btn{background:var(--red)}

/* foods */
.foods{position:absolute;top:1152px;left:0;width:100%;height:364px;background:linear-gradient(135deg,#3c4a1c 0%,#2f3a17 45%,#4a3a1e 75%,#2d3416 100%)}
.foods .section-title{top:40px;color:var(--white)}
.foods .section-lead{top:79px;color:var(--white)}
.food-grid{position:absolute;left:24px;top:128px;display:flex;gap:32px}
.food-item{width:214px}
.food-photo{width:214px;height:160px;border:3px solid var(--white)}
.food-caption{color:var(--white);font-size:14px;font-weight:600;margin-top:14px}

/* info */
.info{position:absolute;top:1516px;left:0;width:100%;height:394px}
.about-box{position:absolute;left:24px;top:53px;width:209px;height:291px;background:var(--green);border:3px solid var(--green);box-shadow:inset 0 0 0 2px var(--white);padding:14px 12px;color:var(--white)}
.about-box h3{font-size:19px}
.about-box .lead{font-size:12.5px;line-height:19px;margin-top:6px}
.about-box p{font-size:10.5px;line-height:22px;margin-top:8px}
.what-we-do{position:absolute;left:276px;top:50px;width:448px}
.what-we-do h3{font-size:17px}
.what-we-do .lead{font-size:11px;line-height:21px;color:var(--green);margin-top:10px}
.what-we-do p{font-size:10.5px;line-height:22px;color:var(--muted);margin-top:6px;padding-bottom:16px;border-bottom:1px solid var(--line)}
.ticks{list-style:none}
.ticks li{display:flex;align-items:center;gap:8px;font-size:11px;color:var(--ink);height:44px;border-bottom:1px solid var(--line)}
.tick-dot{width:11px;height:11px;border-radius:50%;background:var(--green);flex:none;display:flex;align-items:center;justify-content:center}
.featured-post{position:absolute;left:771px;top:53px;width:210px;height:291px;background:var(--red);padding:14px 12px;color:var(--white)}
.featured-post h3{font-size:17px}
.featured-photo{width:184px;height:134px;margin-top:10px;border:2px solid var(--white);background:linear-gradient(135deg,#8e9b74 0%,#d0763f 45%,#b33b1f 70%,#3b3a2a 100%)}
.featured-post .date{font-size:11.5px;margin-top:10px}
.featured-post .excerpt{font-size:10px;line-height:19px;font-style:italic;margin-top:4px}

/* footer */
.site-footer{position:absolute;top:1910px;left:0;width:100%;height:242px;background:var(--footer);color:#ddd}
.footer-brand{position:absolute;left:24px;top:36px;width:260px}
.footer-brand .brand-name{font-size:36px}
.footer-brand p{font-size:10.5px;line-height:19px;margin-top:30px;width:252px;color:#ccc}
.footer-col{position:absolute;top:38px}
.footer-col h4{font-family:"Lobster Two",cursive;font-style:italic;font-weight:700;font-size:14px;color:var(--white)}
.quick-links{left:338px}
.quick-links ul{list-style:none;margin-top:18px}
.quick-links li{font-size:11px;line-height:23px;display:flex;align-items:center;gap:10px}
.quick-links li::before{content:"›";font-size:15px;color:#bbb}
.newsletter{left:485px;width:220px}
.newsletter p{font-size:11px;line-height:19px;margin-top:22px}
.newsletter .field{margin-top:16px;width:215px;height:32px;background:var(--white);border-radius:2px;color:#aaa;font-size:10px;line-height:32px;padding-left:12px}
.newsletter .subscribe{margin-top:10px;width:110px;height:35px;background:var(--red);color:var(--white);font-size:12px;font-weight:700;text-align:center;line-height:35px;border-radius:2px}
.contact{left:768px;width:220px}
.contact .row{display:flex;gap:12px;align-items:flex-start;margin-top:18px;font-size:11px;line-height:19px}
.contact .row.phone{font-size:15px;align-items:center}
.bottom-bar{position:absolute;left:0;top:2152px;width:100%;height:51px;background:var(--green-dark);color:var(--white);display:flex;align-items:center;justify-content:space-between;padding:0 22px 0 24px;font-size:11px}
.social{display:flex;align-items:center;gap:8px}
.social span{width:29px;height:29px;border-radius:50%;border:2px solid var(--white)}
</style>
</head>
<body>
<div class="page">

  <header class="site-header">
    <div class="brand header-brand">
      <span class="brand-dot"></span>
      <span class="brand-name">Saffron Lane</span>
    </div>
    <div class="brand-tag">A fine Pak-Indian Cuisine</div>
    <div class="order-now script">
      <svg width="26" height="34" viewBox="0 0 26 34" aria-hidden="true"><rect x="5" y="2" width="16" height="30" rx="3" fill="none" stroke="#275211" stroke-width="3"/><rect x="9" y="6" width="8" height="18" fill="#275211"/><path d="M2 12q-3 5 0 10" stroke="#275211" stroke-width="2" fill="none"/></svg>
      <span>Order Now! - (+111) 000-0000</span>
    </div>
  </header>

  <nav class="main-nav">
    <a class="active" href="#">Home</a>
    <a href="#">About Us</a>
    <a href="#">Features</a>
    <a href="#">Spices</a>
    <a href="#">Gallery</a>
    <a href="#">Blog</a>
    <a href="#">Contacts</a>
  </nav>

  <section class="hero" role="img" aria-label="Bowls of colourful ground spices, herbs and peppercorns on a wooden table">
    <div class="hero-copy">
      <div class="kicker">WE OFFER</div>
      <div class="headline script">Pakistani and Indian<br>Spice food</div>
    </div>
    <div class="slider-dots"><span class="current"></span><span></span><span></span></div>
  </section>

  <section class="services">
    <h2 class="section-title script">Services We Offer</h2>
    <p class="section-lead">Architecto beatae vitae dicta sunt explicabo. Nemo enim ipsam voluptatem quia voluptas sit aspernatur aut odit aut fugit...</p>
    <div class="pager">‹ ›</div>

    <svg class="service-track" width="1004" height="126" viewBox="0 0 1004 126" aria-hidden="true">
      <line x1="146" y1="63" x2="260" y2="63" stroke="#275211" stroke-width="3"/>
      <line x1="260" y1="63" x2="380" y2="63" stroke="#d6202a" stroke-width="3"/>
      <line x1="503" y1="63" x2="737" y2="63" stroke="#d6202a" stroke-width="3"/>
      <line x1="860" y1="63" x2="981" y2="63" stroke="#d6202a" stroke-width="3"/>
      <circle cx="259" cy="63" r="9" fill="#275211"/>
      <path d="M256 58l5 5-5 5" stroke="#fff" stroke-width="2" fill="none"/>
      <circle cx="616" cy="63" r="9" fill="#d6202a"/>
      <path d="M613 58l5 5-5 5" stroke="#fff" stroke-width="2" fill="none"/>
    </svg>

    <article class="service-card is-green" style="left:24px;top:120px">
      <div class="service-icon"><div class="inner">
        <svg width="48" height="48" viewBox="0 0 48 48" aria-hidden="true"><path d="M34 10c4 4 2 12-6 20s-16 12-20 10c6-2 12-8 16-14s5-12 10-16z" fill="#fff"/><path d="M34 10q2-5 6-6" stroke="#fff" stroke-width="3" fill="none"/></svg>
      </div></div>
      <h3 class="service-title script">Deleniti atque corrupti</h3>
      <p class="service-text">Natur aut odit aut fugit, sed quia consequuntur magni dolores eos qui ratione voluptatem sequi nesciunt. Neque...</p>
      <a class="btn" href="#">READ MORE</a>
    </article>

    <article class="service-card is-red" style="left:381px;top:120px">
      <div class="service-icon"><div class="inner">
        <svg width="46" height="46" viewBox="0 0 46 46" aria-hidden="true"><path d="M36 6l4 4-10 10 4 16-4 4-7-13-8 8v6l-3 3-3-7-7-3 3-3h6l8-8-13-7 4-4 16 4z" fill="#fff"/></svg>
      </div></div>
      <h3 class="service-title script">Encounter consequences</h3>
      <p class="service-text">Natur aut odit aut fugit, sed quia consequuntur magni dolores eos qui ratione voluptatem sequi nesciunt. Neque...</p>
      <a class="btn" href="#">READ MORE</a>
    </article>

    <article class="service-card is-red" style="left:738px;top:120px">
      <div class="service-icon"><div class="inner">
        <svg width="44" height="44" viewBox="0 0 44 44" aria-hidden="true"><circle cx="22" cy="22" r="18" fill="#fff"/><path d="M12 12q6 2 8 8t-4 8l2 8M26 6q2 6 8 6M28 30q4-4 10-2" stroke="#d6202a" stroke-width="3" fill="none"/></svg>
      </div></div>
      <h3 class="service-title script">Encounter consequences</h3>
      <p class="service-text">Natur aut odit aut fugit, sed quia consequuntur magni dolores eos qui ratione voluptatem sequi nesciunt. Neque...</p>
      <a class="btn" href="#">READ MORE</a>
    </article>
  </section>

  <section class="foods">
    <h2 class="section-title script">Our Spice Foods</h2>
    <p class="section-lead">Architecto beatae vitae dicta sunt explicabo. Nemo enim ipsam voluptatem quia voluptas sit aspernatur aut odit aut fugit...</p>
    <div class="food-grid">
      <figure class="food-item">
        <div class="food-photo" role="img" aria-label="Grilled meat taco with corn and purple cabbage" style="background:linear-gradient(135deg,#5e6f7a 0%,#c8894a 45%,#7b3d5e 75%,#4a5560 100%)"></div>
        <figcaption class="food-caption">Nemo enim ipsam volupta</figcaption>
      </figure>
      <figure class="food-item">
        <div class="food-photo" role="img" aria-label="Spicy red curry in a clay bowl with bread" style="background:linear-gradient(135deg,#e6dccd 0%,#b9662f 45%,#9a3c1c 70%,#d8cbb6 100%)"></div>
        <figcaption class="food-caption">Nemo enim ipsam volupta</figcaption>
      </figure>
      <figure class="food-item">
        <div class="food-photo" role="img" aria-label="Plate of pasta with tomato sauce and basil on blue" style="background:linear-gradient(135deg,#0f3b8a 0%,#e9e9ee 35%,#e06d2a 60%,#0c3078 100%)"></div>
        <figcaption class="food-caption">Nemo enim ipsam volupta</figcaption>
      </figure>
      <figure class="food-item">
        <div class="food-photo" role="img" aria-label="Grilled steak with fresh salad on a white plate" style="background:linear-gradient(135deg,#f1f1f1 0%,#b56a3e 45%,#7a3a20 65%,#e9e9e9 100%)"></div>
        <figcaption class="food-caption">Nemo enim ipsam volupta</figcaption>
      </figure>
    </div>
  </section>

  <section class="info">
    <aside class="about-box">
      <h3 class="script">About Us</h3>
      <p class="lead">Similique sunt in culpa qui offi cia deserunt mollitia ani...</p>
      <p>Sed quia non numquam eius modi tempora incidunt ut laboredolore enim ad minima veniam, nostrum exercitationem ullam laboriosam, nisi ut aliquid ex ea consequatur? Quis autem vel eumreprehenderit qui in ea voluptate velit esse quam nihil molestiae consequatur...</p>
    </aside>

    <div class="what-we-do">
      <h3 class="script">What we do</h3>
      <p class="lead">Accusantium doloremque laudantium, totam rem aperiam, eaque ipsa quæ ab illo veritatis et quasi architecto beatæ vitæ dicta sunt explicabo...</p>
      <p>Circumstances occur in which toil and pain can procure him some great pleasure. To take a trivial example, which of us ever undertakes laborious physical exercise, except to obtainadvantage from it? But who has any right to chooses to enjoy...</p>
      <ul class="ticks">
        <li><span class="tick-dot"><svg width="7" height="7" viewBox="0 0 7 7"><path d="M2 1l3 2.5L2 6" stroke="#fff" stroke-width="1.4" fill="none"/></svg></span>Præsentium voluptatum deleniti atque corrupti quos dolores et quas molestias</li>
        <li><span class="tick-dot"><svg width="7" height="7" viewBox="0 0 7 7"><path d="M2 1l3 2.5L2 6" stroke="#fff" stroke-width="1.4" fill="none"/></svg></span>Præsentium voluptatum deleniti atque corrupti quos dolores et quas molestias</li>
        <li><span class="tick-dot"><svg width="7" height="7" viewBox="0 0 7 7"><path d="M2 1l3 2.5L2 6" stroke="#fff" stroke-width="1.4" fill="none"/></svg></span>Præsentium voluptatum deleniti atque corrupti quos dolores et quas molestias</li>
      </ul>
    </div>

    <aside class="featured-post">
      <h3 class="script">Featured Blog Post</h3>
      <div class="featured-photo" role="img" aria-label="Grilled salmon fillet with herbs and cherry tomatoes"></div>
      <p class="date">Posted on 12 Feb 2016</p>
      <p class="excerpt">Sed quia non numquam eius modi enim ad minima veniam, nostrum molestiae consequatur...</p>
    </aside>
  </section>

  <footer class="site-footer">
    <div class="footer-brand">
      <div class="brand">
        <span class="brand-dot"></span>
        <span class="brand-name">Saffron Lane</span>
      </div>
      <p>Lorem Ipsum is simply dummy text of the derit ipariatur. Excepteur sint occaecat cupidatat non proident, sunt in culpa qui officia deserunt and typesetting ipsum text...</p>
    </div>

    <div class="footer-col quick-links">
      <h4>Quick links</h4>
      <ul>
        <li>Home</li><li>About us</li><li>Features</li><li>Spices</li><li>Gallery</li><li>Contact</li>
      </ul>
    </div>

    <div class="footer-col newsletter">
      <h4>Newsletter Signup</h4>
      <p>Lorem ipsum dolor sit amet, consectetur adipiscing elit,</p>
      <div class="field">Email address</div>
      <div class="subscribe">SUBCRIBE</div>
    </div>

    <div class="footer-col contact">
      <h4>Contact Details</h4>
      <div class="row">
        <svg width="12" height="16" viewBox="0 0 12 16" aria-hidden="true"><path d="M6 0a6 6 0 0 1 6 6c0 4-6 10-6 10S0 10 0 6a6 6 0 0 1 6-6z" fill="#fff"/><circle cx="6" cy="6" r="2.2" fill="#262626"/></svg>
        <span>123,Saffron Lane Zee dummy text Street name, #8676 Dummy City name-395001</span>
      </div>
      <div class="row phone">
        <svg width="14" height="14" viewBox="0 0 14 14" aria-hidden="true"><path d="M3 0l3 3-2 2q1 3 5 5l2-2 3 3-2 3Q2 13 0 3z" fill="#fff"/></svg>
        <span>+111-000-0000</span>
      </div>
      <div class="row">
        <svg width="14" height="10" viewBox="0 0 14 10" aria-hidden="true"><rect width="14" height="10" fill="#fff"/><path d="M0 0l7 6 7-6" stroke="#262626" stroke-width="1.4" fill="none"/></svg>
        <span>info@vemrilo.com</span>
      </div>
    </div>
  </footer>

  <div class="bottom-bar">
    <span>Copyright 2015 Saffron Lane. All Rights Reserved</span>
    <div class="social">Connect With Us:
      <span></span><span></span><span></span><span></span><span></span>
    </div>
  </div>

</div>
</body>
</html>
```